SaaS Early tech startup business card design

Unique design for experience ecommerce platform company. the business cards will be used by executive members. conformance with color code is required.

```html
<!DOCTYPE html>
<html lang="en">
<head>
<meta charset="utf-8">
<title>Quorvane Business Card</title>
<link href="https://fonts.googleapis.com/css2?family=Roboto:wght@400;500;700&display=swap" rel="stylesheet">
<style>
  :root {
    --page-bg: #d9d9d9;
    --card-white: #ffffff;
    --brand-navy: #0a5684;
    --brand-teal: #14a98f;
    --rule-blue: #2c6f98;
    --text-grey: #3d3d3d;
    --back-top: #009285;
    --back-bottom: #04567f;
    --logo-white: #ffffff;
  }
  * { margin: 0; padding: 0; box-sizing: border-box; }
  html, body {
    width: 1200px; height: 800px; overflow: hidden;
    background: var(--page-bg);
    font-family: "Roboto", Arial, sans-serif;
  }
  .canvas {
    width: 1200px; height: 800px;
    display: flex; flex-direction: column;
    align-items: center; justify-content: center; gap: 40px;
  }
  .card {
    width: 560px; height: 320px;
    border-radius: 22px;
    position: relative;
    overflow: hidden;
    box-shadow: 0 6px 18px rgba(0,0,0,0.18);
  }
  .card-front { background: var(--card-white); }
  .front-wordmark {
    position: absolute; top: 50px; left: 240px;
    font-size: 52px; font-weight: 700; letter-spacing: -1px;
    color: var(--brand-navy); line-height: 1;
  }
  .front-rule {
    position: absolute; left: 40px; right: 40px; top: 188px;
    height: 1px; background: var(--rule-blue);
  }
  .holder {
    position: absolute; left: 40px; top: 140px;
  }
  .holder-name {
    font-size: 21px; font-weight: 700; color: var(--brand-navy);
    text-transform: uppercase; letter-spacing: 0.3px; line-height: 1.05;
  }
  .holder-title {
    font-size: 15px; font-weight: 500; color: var(--brand-teal); margin-top: 2px;
  }
  .contact-list {
    position: absolute; left: 40px; top: 202px;
    list-style: none;
  }
  .contact-item {
    display: flex; align-items: center; gap: 9px;
    font-size: 14.5px; color: var(--text-grey); line-height: 24px;
  }
  .contact-icon { width: 13px; height: 13px; flex: none; }
  .address {
    position: absolute; right: 40px; top: 202px;
    text-align: right; font-size: 14.5px; font-style: normal;
    color: var(--text-grey); line-height: 22px;
  }
  .card-back {
    background: linear-gradient(160deg, var(--back-top) 0%, var(--back-bottom) 100%);
    display: flex; align-items: center; justify-content: center;
  }
  .back-wordmark {
    font-size: 84px; font-weight: 700; letter-spacing: -2px;
    color: var(--logo-white); line-height: 1;
  }
</style>
</head>
<body>
<main class="canvas">
  <section class="card card-front" aria-label="Business card front">
    <div class="front-wordmark">quorvane</div>
    <div class="holder">
      <div class="holder-name">Daniel Brooks</div>
      <div class="holder-title">President</div>
    </div>
    <div class="front-rule"></div>
    <ul class="contact-list">
      <li class="contact-item">
        <svg class="contact-icon" viewBox="0 0 16 16" aria-hidden="true"><path fill="#14a98f" d="M3.5 1.5l2.5 0 1 3.5-1.8 1.2a8 8 0 0 0 4.6 4.6L11 9l3.5 1v2.5c0 1-1 2-2 2C6.5 14.5 1.5 9.5 1.5 3.5c0-1 1-2 2-2z"/></svg>
        412-308-7741
      </li>
      <li class="contact-item">
        <svg class="contact-icon" viewBox="0 0 16 16" aria-hidden="true"><rect x="4" y="1" width="8" height="14" rx="1.5" fill="none" stroke="#14a98f" stroke-width="1.6"/><circle cx="8" cy="12.5" r="0.9" fill="#14a98f"/></svg>
        412-630-2958
      </li>
      <li class="contact-item">
        <svg class="contact-icon" viewBox="0 0 16 16" aria-hidden="true"><rect x="1" y="3" width="14" height="10" rx="1" fill="#14a98f"/><path d="M1.5 3.5L8 9l6.5-5.5" fill="none" stroke="#fff" stroke-width="1.3"/></svg>
        name@quorvane.com
      </li>
    </ul>
    <address class="address">
      2140 Willowbrook Road<br>
      Fairbanks, Alaska 99701<br>
      www.quorvane.com
    </address>
  </section>

  <section class="card card-back" aria-label="Business card back">
    <div class="back-wordmark">quorvane</div>
  </section>
</main>
</body>
</html>
```